Brookvale Estates LLC stationary for a real estate property management company.

Create stationary (letterhead, envelopes, business cards) using Brookvale Estates LLC logo as primary creative element. Stationary design needs to be horizontal, leaving as much space as possible for correspondence copy. See attached Creative Brief and past stationary files for details.

Target Market(s)

Prospective apartment residents and current residents, vendors, and government agencies.

Industry/Entity Type

Property Management

Contact Information for Business Card

Business card employee title: Property Manager. Should include address, phone, fax, email, website, slogan, and Brookvale Estates logo.

Font styles to use
Sans Serif

Colors
0592cd
000000

Requirements
Must have
• Tone should be conservative, institutional, business (i.e. banking, finance, real estate). Must include: address, phone, fax, website, and slogan (see attached Creative Brief). Should be a horizontal design, leaving as much room as possible for letter correspondence copy.
Nice to have
• Please use an Arial or Helvetica style font.
Should not have
• Letterhead layout should leave as much room as possible for copy.

```html
<!DOCTYPE html>
<html lang="en">
<head>
<meta charset="utf-8">
<title>Brookvale Estates LLC – Business Card</title>
<link rel="stylesheet" href="https://fonts.googleapis.com/css2?family=Arimo:wght@400;700&display=swap">
<style>
  :root {
    --brand-blue: #1273b7;
    --brand-blue-light: #1ab8ec;
    --brand-blue-deep: #0a63a3;
    --charcoal: #4a4a4c;
    --text-grey: #555657;
    --card-white: #f7f7f7;
    --backdrop: #e6e6e6;
  }
  * { box-sizing: border-box; margin: 0; padding: 0; }
  html, body {
    width: 1200px; height: 960px; overflow: hidden;
    background: var(--backdrop);
    font-family: "Arimo", Arial, Helvetica, sans-serif;
  }
  .canvas { position: relative; width: 1200px; height: 960px; }

  .card {
    position: absolute; width: 600px; height: 342px; overflow: hidden;
    box-shadow: 0 3px 8px rgba(0,0,0,.25);
  }

  /* Front */
  .card-front { left: 302px; top: 130px; background: var(--card-white); }
  .brand-lockup {
    position: absolute; left: 50px; top: 170px; width: 240px;
    transform: translateY(-50%);
    display: flex; align-items: center; gap: 12px;
  }
  .brand-square { width: 40px; height: 40px; background: var(--brand-blue); flex: none; }
  .brand-name {
    color: var(--brand-blue); font-weight: 700; font-size: 22px; line-height: 24px;
    letter-spacing: .4px;
  }
  .brand-name span { display: block; white-space: nowrap; }
  .divider {
    position: absolute; left: 307px; top: 85px; width: 1px; height: 180px;
    background: linear-gradient(to bottom, rgba(0,0,0,0), rgba(0,0,0,.35), rgba(0,0,0,0));
  }
  .contact { position: absolute; left: 330px; top: 86px; width: 260px; color: var(--text-grey); }
  .contact-name { color: var(--brand-blue); font-weight: 700; font-size: 21px; line-height: 24px; white-space: nowrap; }
  .contact-title { font-size: 16px; line-height: 20px; margin-bottom: 8px; }
  .contact-address { font-size: 14px; line-height: 19px; margin-bottom: 6px; }
  .contact-list { list-style: none; font-size: 14px; }
  .contact-list li { display: flex; align-items: center; gap: 8px; height: 19.5px; }
  .contact-list svg { width: 14px; height: 14px; fill: var(--brand-blue); flex: none; }

  .footer-band { position: absolute; left: 0; bottom: 0; width: 600px; height: 22px; }

  /* Back */
  .card-back {
    left: 300px; top: 488px;
    background: linear-gradient(135deg, var(--brand-blue-light) 0%, #1391cf 40%, var(--brand-blue-deep) 100%);
    color: #fff; text-align: center;
  }
  .back-brand {
    position: absolute; left: 0; right: 0; top: 128px;
    font-weight: 700; font-size: 36px; letter-spacing: .5px;
  }
  .slogan {
    position: absolute; left: 0; right: 0; top: 288px;
    font-weight: 700; font-size: 16px;
  }
</style>
</head>
<body>
<main class="canvas">
  <section class="card card-front">
    <div class="brand-lockup">
      <span class="brand-square"></span>
      <p class="brand-name"><span>BROOKVALE</span><span>ESTATES LLC</span></p>
    </div>
    <div class="divider"></div>
    <div class="contact">
      <h1 class="contact-name">DANIEL HARGROVE</h1>
      <p class="contact-title">Property Manager</p>
      <p class="contact-address">2750 Alder Creek Drive #B210<br>Fresno, CA 93711</p>
      <ul class="contact-list">
        <li><svg viewBox="0 0 16 16"><path d="M3.6 1.2l2.3 2.6-1.2 1.9c.9 2 2.6 3.7 4.6 4.6l1.9-1.2 2.6 2.3-1.4 2.6C6.6 13.6 2.4 9.4 1 3z"/></svg>559-408-7314</li>
        <li><svg viewBox="0 0 16 16"><path d="M4 1h8v4H4zM1 6h14v6h-2v-2H3v2H1zM4 11h8v4H4z"/></svg>559-408-7320</li>
        <li><svg viewBox="0 0 16 16"><path d="M1 3h14v1L8 9 1 4zM1 6l7 5 7-5v7H1z"/></svg>daniel@brookvaleestates.us</li>
        <li><svg viewBox="0 0 16 16"><path d="M8 1a7 7 0 100 14A7 7 0 008 1zm-1 2.5l1.5 1-1 2 2 1.5-.5 2.5-2 1.5-1-3-2-1 .5-2.5z"/></svg>www.brookvaleestates.us</li>
      </ul>
    </div>
    <svg class="footer-band" viewBox="0 0 600 22" preserveAspectRatio="none" aria-hidden="true">
      <polygon points="0,0 392,0 385,22 0,22" fill="var(--brand-blue)"/>
      <polygon points="398,0 600,0 600,22 391,22" fill="var(--charcoal)"/>
    </svg>
  </section>

  <section class="card card-back">
    <p class="back-brand">BROOKVALE ESTATES LLC</p>
    <p class="slogan">Multifamily Property Management</p>
  </section>
</main>
</body>
</html>
```